Small Business Broker Business Card Design

A business card design for a small business brokerage, which is a financial service, not unlike real estate brokerage, but for small businesses such as laundromats, pizza shops, restaurants, cleaners etc. The designs should all be simple, more conservative in nature, using the colors and font of the logo. Again, think real estate Brokerage as a business context
Contact Information for Business Card
Name: Glen R. Harlow. Title: Small Business Advisor. Email: g.harlow@bayfieldcapitalworks.example. Mobile: (555) 274-3918. Office: (555) 806-2147. www.bayfieldcapitalworks.example

```html
<!DOCTYPE html>
<html lang="en">
<head>
<meta charset="utf-8">
<title>Bayfield Capital Works – Business Card</title>
<link rel="stylesheet" href="https://fonts.googleapis.com/css2?family=Josefin+Sans:wght@600;700&family=Montserrat:wght@400;500;600&display=swap">
<style>
  :root {
    --navy: #1e3a6b;
    --green: #8cc63f;
    --white: #ffffff;
    --ink: #1a1a1a;
    --backdrop: #e6e4e5;
  }
  * { margin: 0; padding: 0; box-sizing: border-box; }
  html, body {
    width: 1200px; height: 1108px; overflow: hidden;
    background: var(--backdrop);
  }
  .canvas { position: relative; width: 1200px; height: 1108px; }
  .card { position: absolute; width: 729px; height: 437px; }
  .card--front { left: 237px; top: 67px; background: var(--white); }
  .card--back { left: 244px; top: 580px; background: var(--navy); }

  .brand-mark {
    position: absolute; display: flex; flex-direction: column; align-items: center; gap: 14px;
    font-family: "Josefin Sans", sans-serif; font-weight: 700; font-size: 30px; letter-spacing: 3px;
  }
  .brand-mark__square { width: 62px; height: 62px; background: var(--green); }
  .card--front .brand-mark { left: 124px; top: 150px; width: 178px; color: var(--navy); }
  .card--back .brand-mark { left: 270px; top: 125px; width: 188px; color: var(--white); }

  .divider { position: absolute; left: 338px; top: 120px; width: 2px; height: 176px; background: var(--navy); }
  .contact { position: absolute; left: 354px; top: 118px; font-family: "Montserrat", sans-serif; color: var(--ink); }
  .contact__name {
    font-family: "Josefin Sans", sans-serif; font-weight: 700; font-size: 26px;
    color: var(--navy); line-height: 1; letter-spacing: 0.2px;
  }
  .contact__title { font-size: 15.5px; margin-top: 6px; }
  .contact__list { list-style: none; margin-top: 18px; font-size: 15.5px; }
  .contact__list li { height: 30.3px; line-height: 30.3px; }
  .contact__label { color: var(--navy); font-weight: 600; margin-right: 4px; }

  .company { position: absolute; left: 0; width: 100%; text-align: center; }
  .card--front .company { top: 352px; }
  .card--back .company { top: 278px; }
  .company__name {
    font-family: "Josefin Sans", sans-serif; font-weight: 700; font-size: 30px;
    color: var(--navy); line-height: 1; letter-spacing: 1px;
  }
  .card--back .company__name { color: var(--white); }
  .company__tagline {
    font-family: "Montserrat", sans-serif; font-weight: 600; font-size: 14.5px;
    color: var(--green); letter-spacing: 2.3px; margin-top: 5px;
  }
</style>
</head>
<body>
<main class="canvas">
  <section class="card card--front">
    <div class="brand-mark"><span class="brand-mark__square"></span>BAYFIELD</div>
    <div class="divider"></div>
    <div class="contact">
      <h1 class="contact__name">GLEN R. HARLOW</h1>
      <p class="contact__title">Small Business Advisor</p>
      <ul class="contact__list">
        <li><span class="contact__label">M:</span>(555) 274-3918</li>
        <li><span class="contact__label">O:</span>(555) 806-2147</li>
        <li><span class="contact__label">E:</span>g.harlow@bayfieldcapitalworks.example</li>
        <li><span class="contact__label">W:</span>www.bayfieldcapitalworks.example</li>
      </ul>
    </div>
    <div class="company">
      <p class="company__name">BAYFIELD CAPITAL WORKS, INC</p>
      <p class="company__tagline">TRUSTED GUIDANCE TO BUY OR SELL YOUR BUSINESS</p>
    </div>
  </section>

  <section class="card card--back">
    <div class="brand-mark"><span class="brand-mark__square"></span>BAYFIELD</div>
    <div class="company">
      <p class="company__name">BAYFIELD CAPITAL WORKS, INC</p>
      <p class="company__tagline">TRUSTED GUIDANCE TO BUY OR SELL YOUR BUSINESS</p>
    </div>
  </section>
</main>
</body>
</html>
```